TL - business card

Tallow Partners is an insurance brokerage firm, inovative, proactive, vigorous, which aims to become the leader of the insurance brokers in Anfrica. We should like to get some designs which should be avoided also in Gray / Metallic for the Administration and Orange / Blue for the Managers (ike in the picture sent). The Blue / Green logo is not the correct one, but the source of the file. Please adjust the color accordingly for the business cards. 1 / Orange / Blue 2 / Gray / Metallic We want something classic but which is transmitted strenght, inovation, modernity and most of all, rapidity. We want something start-up like, very punchy and catching eye remaining profesional at the same time. Name: Dorian Whitlock Function: Managing Director Address: N ° 17/18 Rua Veloso - R / C 2B Direita - Bairro Mutamba - Luanda Tel: (+244) 947 582 316 Email: dorian.whitlock@tallow-p.example Website: www.tallow-p. example We want classic in the front and creative, colorfull at the back. The cards will be printed in relief, with very high quality of paper.
Insurance Broker
Colors
Designer to choose colors to be used in the design.

```html
<!DOCTYPE html>
<html lang="en">
<head>
<meta charset="utf-8">
<title>Tallow Partners – Business Card</title>
<link href="https://fonts.googleapis.com/css2?family=Roboto:wght@400;500;700&display=swap" rel="stylesheet">
<style>
  :root {
    --backdrop: #e4e4e4;
    --card-dark: #1c1d1f;
    --card-green: #009444;
    --brand-green: #0e9a48;
    --brand-blue: #2aa3e0;
    --text-light: #f2f2f2;
    --divider: #8a8a8a;
    --white: #ffffff;
  }
  * { box-sizing: border-box; margin: 0; padding: 0; }
  html, body { width: 1200px; height: 801px; overflow: hidden; }
  body {
    background: var(--backdrop);
    font-family: "Roboto", Arial, sans-serif;
    position: relative;
  }
  .card {
    position: absolute;
    top: 250px;
    width: 525px;
    height: 300px;
    border-radius: 2px;
    box-shadow: 0 8px 22px rgba(0,0,0,0.22);
    overflow: hidden;
  }
  .card--front { left: 45px; background: var(--card-dark); }
  .card--back { left: 630px; background: var(--card-green); }

  .brand {
    position: absolute;
    left: 30px;
    top: 0;
    width: 210px;
    height: 100%;
    display: flex;
    flex-direction: column;
    align-items: center;
    justify-content: center;
    gap: 14px;
  }
  .brand__dot {
    width: 58px; height: 58px;
    border-radius: 50%;
    background: var(--brand-blue);
  }
  .brand__name {
    color: var(--brand-green);
    font-weight: 700;
    font-size: 22px;
    letter-spacing: 0.5px;
    text-transform: uppercase;
    white-space: nowrap;
  }

  .divider {
    position: absolute;
    left: 262px;
    top: 38px;
    width: 1px;
    height: 224px;
    background: linear-gradient(to bottom, transparent, var(--divider) 20%, var(--divider) 80%, transparent);
  }

  .details {
    position: absolute;
    left: 285px;
    top: 50px;
    width: 230px;
    color: var(--text-light);
  }
  .details__name { color: var(--brand-green); font-weight: 700; font-size: 21px; line-height: 1.1; }
  .details__role { color: var(--brand-blue); font-weight: 500; font-size: 13px; margin-top: 3px; }
  .details__address { font-size: 11.5px; line-height: 1.45; margin-top: 12px; }
  .contact { list-style: none; margin-top: 12px; font-size: 11.5px; line-height: 1.6; }
  .contact li { display: flex; align-items: center; gap: 7px; white-space: nowrap; }
  .contact svg { width: 11px; height: 11px; flex: none; fill: var(--brand-green); }

  .back-brand {
    position: absolute;
    left: 0; right: 0; top: 95px;
    text-align: center;
    color: var(--white);
    font-weight: 700;
    font-size: 34px;
    text-transform: uppercase;
    letter-spacing: 1px;
  }
  .back-web {
    position: absolute;
    left: 0; right: 0; bottom: 58px;
    text-align: center;
    color: var(--white);
    font-size: 13px;
    letter-spacing: 7px;
  }
</style>
</head>
<body>
  <section class="card card--front">
    <div class="brand">
      <div class="brand__dot"></div>
      <div class="brand__name">Tallow Partners</div>
    </div>
    <div class="divider"></div>
    <div class="details">
      <p class="details__name">Dorian Whitlock</p>
      <p class="details__role">Managing Director</p>
      <p class="details__address">N ° 17/18 Rua Veloso<br>R / C 2B Direita<br>Bairro Mutamba, Luanda</p>
      <ul class="contact">
        <li><svg viewBox="0 0 24 24"><path d="M6.6 10.8a15 15 0 0 0 6.6 6.6l2.2-2.2c.3-.3.7-.4 1-.2 1.1.4 2.3.6 3.6.6.6 0 1 .4 1 1V20c0 .6-.4 1-1 1A17 17 0 0 1 3 4c0-.6.4-1 1-1h3.5c.6 0 1 .4 1 1 0 1.3.2 2.5.6 3.6.1.3 0 .7-.2 1z"/></svg>(+244) 947 582 316</li>
        <li><svg viewBox="0 0 24 24"><path d="M2 5h20v14H2z M2 5l10 7 10-7" /></svg>dorian.whitlock@tallow-p.example</li>
        <li><svg viewBox="0 0 24 24"><circle cx="12" cy="12" r="10"/></svg>www.tallow-p. example</li>
      </ul>
    </div>
  </section>

  <section class="card card--back">
    <p class="back-brand">Tallow Partners</p>
    <p class="back-web">www.tallow-p.example</p>
  </section>
</body>
</html>
```